Website for new child psychology practice

New clinical psychology practice in NSW Australia, specialising in work with children, adolescents and families. I would like to feature the colours in the logo, which was recently designed by pixelharbor designer Odette.
I am seeking a professional looking page, which is easy to navigate and is colourful and playful but not childish.
Target Market(s)
Parents and professionals
Industry/Entity Type
Health
Coding
Coded - Design and coding required
Number of Pages Required
1 page
Font styles to use
Serif
Requirements
Must have
- Pages for 'About us' 'Services' 'Fees and information' 'Contact us'
Should not have
- Childish stock photos

```html
<!DOCTYPE html>
<html lang="en">
<head>
<meta charset="utf-8">
<title>Dr Clara Hayes – Clinical Psychologist</title>
<link rel="stylesheet" href="https://fonts.googleapis.com/css2?family=Lato:wght@400;700&family=Roboto+Condensed:wght@700&family=Roboto:wght@700;900&display=swap">
<style>
:root{
  --purple:#9e2a8d;
  --purple-soft:#a8608f;
  --orange:#ee7d3b;
  --peach:#f4c27e;
  --cream:#fdf3e6;
  --ink:#2b2b2b;
  --text:#333;
  --grey-band:#ececec;
  --black:#050505;
}
*{box-sizing:border-box;margin:0;padding:0}
html,body{width:1200px;height:3627px;overflow:hidden;background:#fff}
body{position:relative;font-family:'Lato',sans-serif;color:var(--text)}
.abs{position:absolute}
.topbar{left:0;top:0;width:1200px;height:6px;background:var(--purple)}
.brand{display:flex;align-items:center;gap:10px}
.brand-dot{width:30px;height:30px;border-radius:50%;background:var(--purple)}
.brand-name{font-family:'Lato',sans-serif;font-weight:700;font-size:27px;color:var(--ink);letter-spacing:.5px}
.header .brand{left:113px;top:40px}
.info{display:flex;align-items:center;gap:20px;font-size:14px;color:#444}
.info-icon{width:44px;height:44px;border-radius:50%;border:1.5px solid var(--purple);display:flex;align-items:center;justify-content:center}
.divider-v{left:671px;top:44px;width:1px;height:30px;background:#e4cfa9}
.divider-v2{left:906px;top:44px;width:1px;height:30px;background:#e4cfa9}
.btn{display:flex;align-items:center;justify-content:center;background:var(--orange);color:#fff;border-radius:30px;font-family:'Roboto Condensed',sans-serif;font-weight:700;font-size:13px;text-transform:uppercase}
.nav{left:0;top:107px;width:1200px;height:69px;background:var(--peach)}
.nav-home{left:0;top:0;width:183px;height:69px;background:var(--purple-soft)}
.nav a{position:absolute;top:25px;font-size:15px;color:#3a2a1a;text-decoration:none}
.search{left:895px;top:20px;width:190px;height:26px;border-bottom:1px solid #c7a36b;font-size:14px;color:#4a3a2a}
.hero{left:0;top:176px;width:1200px;height:725px;background:linear-gradient(180deg,#5c6e86 0%,#8a8f98 35%,#a88d70 60%,#4d5a66 100%)}
.hero-title{left:110px;top:262px;font-family:'Roboto',sans-serif;font-size:92px;line-height:100px;color:#fff}
.hero-title b{font-weight:900}
.hero-title span{font-weight:400;letter-spacing:3px}
.hero-sub{left:110px;top:466px;width:500px;font-size:21px;line-height:35px;color:#fff}
.h2{display:flex;align-items:center;gap:12px;font-family:'Roboto',sans-serif;font-weight:700;font-size:34px;color:var(--ink)}
.h2::before{content:"";width:30px;height:30px;border-radius:50%;background:var(--purple)}
.copy{font-size:14.5px;line-height:25.7px;text-align:justify;color:var(--text)}
.services{left:0;top:1474px;width:1200px;height:539px;background:radial-gradient(circle at 50% 40%,#f3f3f3,var(--grey-band))}
.card{top:1643px;width:228px;height:276px;background:#fff;border-radius:10px;box-shadow:0 2px 10px rgba(0,0,0,.15)}
.card-img{position:absolute;left:10px;top:10px;width:208px;height:197px}
.card-cap{position:absolute;left:16px;top:232px;width:196px;display:flex;justify-content:space-between;align-items:center;font-family:'Roboto',sans-serif;font-weight:700;font-size:13.5px;color:var(--purple)}
.card-cap i{width:12px;height:12px;border-radius:50%;background:#333;display:inline-block}
.arrow{width:38px;height:38px;border-radius:50%;display:flex;align-items:center;justify-content:center}
.contact{left:0;top:2622px;width:1200px;height:600px;background:var(--cream)}
.field{height:56px;border:1.5px solid #d9c9b6;border-radius:30px;background:#fff;box-shadow:0 2px 4px rgba(0,0,0,.08);padding-left:27px;display:flex;align-items:center;font-family:Arial,sans-serif;font-size:14px;color:#555}
.footer{left:0;top:3160px;width:1200px;height:467px;background:var(--black)}
.f-head{font-family:'Roboto',sans-serif;font-weight:700;font-size:19px;color:#fff}
.f-list{list-style:none;font-size:14.5px;color:#fff}
.f-list li{height:25.7px;display:flex;align-items:center;gap:12px}
.f-list li::before{content:"»";font-size:16px}
.social{width:35px;height:35px;border-radius:50%;border:1.5px solid #fff}
.f-contact{font-size:14.5px;color:#fff;line-height:25px;display:flex;gap:10px}
.rule{left:113px;top:3548px;width:1028px;height:1px;background:#333}
.copyright{left:0;top:3576px;width:1200px;text-align:center;font-size:14.5px;color:#fff}
</style>
</head>
<body>

<div class="abs topbar"></div>

<header class="header">
  <div class="abs brand"><span class="brand-dot"></span><span class="brand-name">DR CLARA HAYES</span></div>
  <div class="abs info" style="left:481px;top:37px">
    <span class="info-icon"><svg width="18" height="22" viewBox="0 0 18 22"><path d="M9 21s7-7.5 7-12.5A7 7 0 0 0 2 8.5C2 13.5 9 21 9 21z" fill="none" stroke="#9e2a8d" stroke-width="1.5"/><circle cx="9" cy="8.5" r="2.5" fill="none" stroke="#9e2a8d" stroke-width="1.5"/></svg></span>
    NSW Australia
  </div>
  <div class="abs divider-v"></div>
  <div class="abs info" style="left:697px;top:37px">
    <span class="info-icon"><svg width="20" height="20" viewBox="0 0 20 20"><path d="M4 2l4 1 1 4-2 2a11 11 0 0 0 4 4l2-2 4 1 1 4-3 2C8 18 2 12 2 5z" fill="none" stroke="#9e2a8d" stroke-width="1.4"/></svg></span>
    +1 (555) 010 2020
  </div>
  <div class="abs divider-v2"></div>
  <a class="abs btn" style="left:929px;top:35px;width:159px;height:47px">Free Consultation</a>
</header>

<nav class="abs nav">
  <div class="abs nav-home"></div>
  <a style="left:120px;color:#fff">HOME</a>
  <a style="left:224px">ABOUT US</a>
  <a style="left:352px">SERVICES</a>
  <a style="left:476px">FEES AND INFORMATION</a>
  <a style="left:712px">CONTACT US</a>
  <div class="abs search">Search
    <svg class="abs" style="right:4px;top:3px" width="14" height="14" viewBox="0 0 14 14"><circle cx="6" cy="6" r="4.3" fill="none" stroke="#333" stroke-width="2"/><path d="M9 9l4 4" stroke="#333" stroke-width="2"/></svg>
  </div>
</nav>

<section class="abs hero" role="img" aria-label="Harbour city skyline and bridge at sunset"></section>
<h1 class="abs hero-title"><b>DR.CLARA</b><br><span>HAYES</span></h1>
<p class="abs hero-sub">Specialising in work with children, adolescents and families</p>
<a class="abs btn" style="left:113px;top:556px;width:159px;height:47px">Free Consultation</a>

<svg class="abs" style="left:0;top:690px" width="1200" height="215" viewBox="0 690 1200 215">
  <path d="M0 812 C180 720 360 705 640 785 C820 835 1000 860 1200 790 L1200 905 L0 905Z" fill="#fff"/>
  <path d="M0 905 L0 815 C150 730 340 705 635 790 C420 770 200 800 0 905Z" fill="#9e2a8d"/>
  <path d="M570 713 C740 760 840 855 990 852 C1090 848 1150 808 1200 785 L1200 838 C1100 880 930 900 820 872 C710 842 640 765 570 713Z" fill="#f4c27e"/>
</svg>

<section id="about">
  <div class="abs" style="left:104px;top:890px;width:495px;height:495px;border-radius:50%;border:4px solid var(--orange);clip-path:inset(0 0 0 50%)"></div>
  <div class="abs" role="img" aria-label="Psychologist talking with a young girl at a table" style="left:110px;top:906px;width:464px;height:464px;border-radius:50%;background:linear-gradient(135deg,#e9e2d8,#cdbfae 55%,#8a7b6a)"></div>
  <h2 class="abs h2" style="left:631px;top:945px">ABOUT US</h2>
  <p class="abs copy" style="left:631px;top:1019px;width:453px">Lorem ipsum dolor sit amet, consectetur adipiscing elit, sed do eiusmod tempor incididunt ut labore et dolore magna aliqua. Ut enim ad minim veniam, quis nostrud exercitation ullamco laboris nisi ut aliquip ex ea commodo consequat. Duis aute irure dolor in reprehenderit in voluptate velit esse cillum dolore eu fugiat nulla pariatur. Excepteur sint occaecat cupidatat non proident, sunt in culpa qui officia deserunt mollit anim id est laborum. Sed ut perspiciatis unde omnis iste natus error sit voluptatem accusantium doloremque laudantium, totam rem.</p>
  <a class="abs btn" style="left:631px;top:1284px;width:125px;height:45px">Learn More</a>
</section>

<section id="services">
  <div class="abs services" role="img" aria-label="Faint tree texture"></div>
  <h2 class="abs h2" style="left:457px;top:1565px">OUR SERVICES</h2>
  <div class="abs card" style="left:113px"><div class="card-img" role="img" aria-label="Therapist taking notes with an older client" style="background:linear-gradient(135deg,#d9d4cc,#8d98a6)"></div><div class="card-cap">Lorem ipsum dolor <i></i></div></div>
  <div class="abs card" style="left:362px"><div class="card-img" role="img" aria-label="Counsellor in a bright consulting room" style="background:linear-gradient(135deg,#e4ddd2,#a89a88)"></div><div class="card-cap">Lorem ipsum dolor <i></i></div></div>
  <div class="abs card" style="left:611px"><div class="card-img" role="img" aria-label="Happy family on a sofa" style="background:linear-gradient(135deg,#cfc6bb,#8a8f9c)"></div><div class="card-cap">Lorem ipsum dolor <i></i></div></div>
  <div class="abs card" style="left:859px"><div class="card-img" role="img" aria-label="Child drawing with a therapist" style="background:linear-gradient(135deg,#eae6df,#9fb4a0)"></div><div class="card-cap">Lorem ipsum dolor <i></i></div></div>
  <div class="abs arrow" style="left:51px;top:1762px;border:1.5px solid var(--orange)"><svg width="12" height="14" viewBox="0 0 12 14"><path d="M8 2L3 7l5 5" fill="none" stroke="#ee7d3b" stroke-width="2"/></svg></div>
  <div class="abs arrow" style="left:1103px;top:1762px;background:var(--orange)"><svg width="12" height="14" viewBox="0 0 12 14"><path d="M4 2l5 5-5 5" fill="none" stroke="#fff" stroke-width="2"/></svg></div>
</section>

<section id="fees">
  <h2 class="abs h2" style="left:114px;top:2125px">FEES AND INFORMATION</h2>
  <p class="abs copy" style="left:114px;top:2199px;width:453px">Lorem ipsum dolor sit amet, consectetur adipiscing elit, sed do eiusmod tempor incididunt ut labore et dolore magna aliqua. Ut enim ad minim veniam, quis nostrud exercitation ullamco laboris nisi ut aliquip ex ea commodo consequat. Duis aute irure dolor in reprehenderit in voluptate velit esse cillum dolore eu fugiat nulla pariatur. Excepteur sint occaecat cupidatat non proident, sunt in culpa qui officia deserunt mollit anim id est laborum. Sed ut perspiciatis unde omnis iste natus error sit voluptatem accusantium doloremque laudantium, totam rem.</p>
  <a class="abs btn" style="left:114px;top:2464px;width:125px;height:45px">Learn More</a>
  <div class="abs" role="img" aria-label="Collage of sunset photographs in a cluster of rounded shapes" style="left:615px;top:2126px;width:470px;height:390px;border-radius:50%;background:radial-gradient(circle at 45% 45%,#c0652c,#8e2482 55%,#3a1a3a)"></div>
</section>

<section id="contact">
  <div class="abs contact"></div>
  <h2 class="abs h2" style="left:470px;top:2690px">CONTACT US</h2>
  <div class="abs field" style="left:170px;top:2771px;width:420px">First Name :</div>
  <div class="abs field" style="left:608px;top:2771px;width:421px">Last Name :</div>
  <div class="abs field" style="left:170px;top:2851px;width:420px">Email :</div>
  <div class="abs field" style="left:608px;top:2851px;width:421px">Phone :</div>
  <div class="abs field" style="left:170px;top:2936px;width:858px">Message :</div>
  <a class="abs btn" style="left:517px;top:3029px;width:166px;height:55px;font-family:'Lato',sans-serif;font-size:16px">Submit</a>
</section>

<footer>
  <div class="abs footer"></div>
  <svg class="abs" style="left:0;top:3060px" width="1200" height="210" viewBox="0 3060 1200 210">
    <path d="M0 3070 C100 3150 300 3185 627 3183 C400 3200 150 3210 0 3168Z" fill="#9e2a8d"/>
    <path d="M0 3168 C150 3210 400 3200 627 3183 C380 3240 250 3270 0 3270Z" fill="#050505"/>
    <path d="M570 3252 C760 3170 950 3090 1200 3119 L1200 3266 C1100 3220 900 3200 570 3252Z" fill="#f4c27e"/>
  </svg>
  <div class="abs brand" style="left:113px;top:3370px"><span class="brand-dot"></span><span class="brand-name" style="color:#fff">DR CLARA HAYES</span></div>
  <div class="abs social" style="left:113px;top:3441px"></div>
  <div class="abs social" style="left:157px;top:3441px"></div>
  <div class="abs social" style="left:199px;top:3441px"></div>
  <div class="abs social" style="left:242px;top:3441px"></div>
  <div class="abs social" style="left:285px;top:3441px"></div>

  <h3 class="abs f-head" style="left:450px;top:3328px">Quick Links</h3>
  <ul class="abs f-list" style="left:450px;top:3365px"><li>Home</li><li>About Us</li><li>Services</li><li>Fees and Information</li><li>Contact Us</li></ul>

  <h3 class="abs f-head" style="left:680px;top:3328px">Other Links</h3>
  <ul class="abs f-list" style="left:680px;top:3365px"><li>Terms &amp; Conditions</li><li>Privacy Policy</li><li>About Us</li><li>Support</li></ul>

  <h3 class="abs f-head" style="left:899px;top:3328px">Contact us</h3>
  <div class="abs f-contact" style="left:899px;top:3366px"><svg width="13" height="18" viewBox="0 0 13 18"><path d="M6.5 17S12 10 12 6.5a5.5 5.5 0 0 0-11 0C1 10 6.5 17 6.5 17z" fill="#fff"/><circle cx="6.5" cy="6.5" r="2" fill="#050505"/></svg><span>Dr.Clara Hayes<br>NSW Australia</span></div>
  <div class="abs f-contact" style="left:899px;top:3434px"><svg width="15" height="15" viewBox="0 0 20 20"><path d="M4 2l4 1 1 4-2 2a11 11 0 0 0 4 4l2-2 4 1 1 4-3 2C8 18 2 12 2 5z" fill="#fff"/></svg><span>+1 (555) 010 2020</span></div>
  <div class="abs f-contact" style="left:899px;top:3476px"><svg width="16" height="13" viewBox="0 0 16 13"><rect x="0" y="1" width="16" height="11" fill="#fff"/><path d="M0 1l8 6 8-6" fill="none" stroke="#050505" stroke-width="1.3"/></svg><span>info@drclarahayes.com</span></div>

  <div class="abs rule"></div>
  <p class="abs copyright">©Copyrights 2024 Dr.Clara Hayes &nbsp;&nbsp;|&nbsp;&nbsp; All Rights Reserved</p>
</footer>

</body>
</html>
```